Blockchain Analytics Firm Needs Logo And Website Design

We need a logo and a very basic website for a company based in Linköping, Sweden called 'Vextor'. We build custom machine learning and AI solutions for companies based on blockchain. We are not picky about the colors, but the design should communicate modernity and stability.
We like the following websites:
https://www.pallidwren.co.uk/
https://www.tormacapitalhouse.com/
Target Market(s)
Our customers are startups that have their own product based on blockchain or other distributed ledger technology.
Industry/Entity Type
It Company
Contact Information for Business Card
Name, title and email address
Logo Text
Our company name and "Blockchain Analytics"
Font styles to use
Colors
Designer to choose colors to be used in the design.
Requirements
Must have
- The website and logo need to be modern and clean. In the beginning, we will not be filling out all sections of the website (team, clients, etc.) but we will need to have these set up so we can eventually use them.
Nice to have
- We like angular graphics and some animations on the webpage would be nice.

```html
<!DOCTYPE html>
<html lang="en">
<head>
<meta charset="utf-8">
<title>Vextor — Blockchain Analytics</title>
<link rel="stylesheet" href="https://fonts.googleapis.com/css2?family=Questrial&family=Open+Sans:wght@400;600&display=swap">
<style>
:root{
  --header-bg:#262626;
  --footer-bg:#222222;
  --accent-red:#e8453c;
  --brand-blue:#3aa6e8;
  --violet:#7a4be6;
  --hero-a:#8a3df0;
  --hero-b:#5b7cf2;
  --hero-c:#4fc3f7;
  --text-dark:#333333;
  --text-mid:#555555;
  --text-light:#cfcfcf;
  --text-muted:#8a8a8a;
  --band-bg:#efefef;
  --diamond:#262626;
  --white:#ffffff;
}
*{box-sizing:border-box;margin:0;padding:0}
html,body{width:1200px;height:2821px;overflow:hidden}
body{position:relative;background:var(--white);font-family:"Open Sans",Arial,sans-serif;color:var(--text-dark)}
.abs{position:absolute}

/* header */
.site-header{left:0;top:0;width:1200px;height:130px;background:var(--header-bg)}
.brand{left:132px;top:34px;display:flex;align-items:center;gap:14px}
.brand-mark{width:40px;height:40px;background:var(--accent-red)}
.brand-name{font-family:"Questrial",sans-serif;font-size:36px;color:var(--accent-red);letter-spacing:1px}
.member-login{left:946px;top:24px;width:120px;height:33px;background:var(--accent-red);color:var(--white);font-family:"Questrial",sans-serif;font-size:14px;border-radius:3px;display:flex;align-items:center;justify-content:center}
.main-nav{right:134px;top:82px;display:flex;gap:30px;font-family:"Questrial",sans-serif;font-size:15px;color:var(--white)}
.main-nav .current{color:var(--brand-blue)}

/* hero */
.hero{left:0;top:130px;width:1200px;height:485px;background:linear-gradient(120deg,var(--hero-a) 0%,var(--hero-b) 50%,var(--hero-c) 100%)}
.hero-title{left:0;top:290px;width:1200px;text-align:center;font-family:"Questrial",sans-serif;font-size:37px;line-height:47px;color:var(--white)}
.hero-btn{left:540px;top:397px;width:120px;height:46px;background:var(--white);color:var(--accent-red);font-family:"Questrial",sans-serif;font-size:15px;display:flex;align-items:center;justify-content:center}
.hero-arrow{top:358px}

/* welcome */
.welcome-title{left:0;top:688px;width:1200px;text-align:center;font-family:"Questrial",sans-serif;font-size:37px;color:var(--accent-red)}
.welcome-text{left:132px;top:740px;width:936px;text-align:center;font-size:15.5px;line-height:29px;color:var(--text-dark)}
.dashboard-shot{left:132px;top:890px;width:936px;height:551px;background:linear-gradient(90deg,#24323d 0%,#24323d 16%,#e9edf0 16%,#f3f4f6 100%)}

/* video */
.video-block{left:0;top:1520px;width:1200px;height:402px;background:linear-gradient(120deg,#2f2f33 0%,#1a1a1c 60%,#3a322c 100%)}
.play-btn{left:570px;top:1691px}

/* features */
.feature{top:2000px;width:320px;text-align:center}
.feature-diamond{margin:0 auto;width:216px;height:216px;display:block}
.feature-title{margin-top:14px;font-family:"Questrial",sans-serif;font-size:23px;color:var(--violet);letter-spacing:.5px}
.feature-text{margin-top:8px;font-size:13px;line-height:20px;color:var(--text-dark)}

/* partners */
.partners{left:0;top:2389px;width:1200px;height:118px;background:var(--band-bg)}
.partner{top:2432px;width:130px;text-align:center;font-family:"Questrial",sans-serif;font-size:20px;color:#1e1e1e;letter-spacing:1px}

/* footer */
.site-footer{left:0;top:2507px;width:1200px;height:314px;background:var(--footer-bg)}
.footer-head{top:2560px;font-family:"Questrial",sans-serif;font-size:15px;color:var(--text-light);letter-spacing:.5px}
.footer-link{font-size:12px;color:var(--text-muted)}
.field{border:1px solid #4a4a4a;color:var(--text-muted);font-size:12px;padding:8px 14px;background:transparent}
.send-btn{left:1012px;top:2637px;width:55px;height:32px;background:#4a4a4a;color:var(--text-light);font-size:12px;display:flex;align-items:center;justify-content:center}
.footer-rule{left:132px;top:2718px;width:936px;height:1px;background:#3c3c3c}
.copyright{left:132px;top:2758px;font-size:11px;color:var(--text-muted)}
.social-dot{top:2760px;width:14px;height:14px;border-radius:50%;background:#6a6a6a}
</style>
</head>
<body>

<header class="abs site-header">
  <div class="abs brand"><span class="brand-mark"></span><span class="brand-name">VEXTOR</span></div>
  <div class="abs member-login">Member Login</div>
  <nav class="abs main-nav">
    <span class="current">Home</span><span>Services</span><span>Portfolio</span><span>About</span><span>Partners</span><span>Contact Us</span>
  </nav>
</header>

<section class="abs hero" role="img" aria-label="Angular low-poly background in violet and blue tones"></section>
<h1 class="abs hero-title">Pellentesque imperdiet dolor<br>et auctor est</h1>
<div class="abs hero-btn">Learn More</div>
<svg class="abs hero-arrow" style="left:52px" width="20" height="30" viewBox="0 0 20 30"><polyline points="15,4 5,15 15,26" fill="none" stroke="#fff" stroke-width="3"/></svg>
<svg class="abs hero-arrow" style="left:1128px" width="20" height="30" viewBox="0 0 20 30"><polyline points="5,4 15,15 5,26" fill="none" stroke="#fff" stroke-width="3"/></svg>

<h2 class="abs welcome-title">Welcome to Vextor</h2>
<p class="abs welcome-text">Vextor is a data analytics startup that can quickly deploy custom machine learning and AI solutions for companies based on Distributed Ledger Technologies (DLT) such as Blockchains.&nbsp; A massive amount of data is generated from these Smart Contracts, particularly from Internet of Things (IoT) applications.&nbsp; We combine this information with traditional data pipelines and present a complete package to our customer.</p>
<div class="abs dashboard-shot" role="img" aria-label="Analytics dashboard screenshot with sidebar, stat cards, charts and order table"></div>

<section class="abs video-block" role="img" aria-label="Video still of a speaker presenting on stage"></section>
<svg class="abs play-btn" width="60" height="60" viewBox="0 0 60 60"><circle cx="30" cy="30" r="29" fill="#fff"/><polygon points="24,18 42,30 24,42" fill="#222"/></svg>

<div class="abs feature" style="left:118px">
  <svg class="feature-diamond" viewBox="0 0 216 216"><polygon points="108,0 216,108 108,216 0,108" fill="var(--diamond)"/>
    <g fill="none" stroke="#fff" stroke-width="2.5"><rect x="86" y="112" width="8" height="20"/><rect x="100" y="102" width="8" height="30"/><rect x="114" y="92" width="8" height="40"/><rect x="128" y="84" width="8" height="48"/><polyline points="82,104 100,88 112,94 134,74"/><polyline points="124,74 134,74 134,84"/></g></svg>
  <div class="feature-title">MAECENAS VEL</div>
  <p class="feature-text">As more and more people own cryptocurrencies, interest in using them as a means of payment increases.</p>
</div>
<div class="abs feature" style="left:440px">
  <svg class="feature-diamond" viewBox="0 0 216 216"><polygon points="108,0 216,108 108,216 0,108" fill="var(--diamond)"/>
    <g fill="none" stroke="#fff" stroke-width="2.5"><rect x="80" y="78" width="18" height="18"/><rect x="118" y="78" width="18" height="18"/><rect x="80" y="118" width="18" height="18"/><rect x="118" y="118" width="18" height="18"/><line x1="98" y1="87" x2="118" y2="87"/><line x1="89" y1="96" x2="89" y2="118"/><line x1="127" y1="96" x2="127" y2="118"/><line x1="98" y1="127" x2="118" y2="127"/></g></svg>
  <div class="feature-title">AENEAN FACILISIS</div>
  <p class="feature-text">As more and more people own cryptocurrencies, interest in using them as a means of payment increases.</p>
</div>
<div class="abs feature" style="left:762px">
  <svg class="feature-diamond" viewBox="0 0 216 216"><polygon points="108,0 216,108 108,216 0,108" fill="var(--diamond)"/>
    <g fill="none" stroke="#fff" stroke-width="3"><circle cx="102" cy="100" r="20"/><line x1="116" y1="114" x2="136" y2="134"/></g></svg>
  <div class="feature-title">VIVAMUS EFFICITUR</div>
  <p class="feature-text">As more and more people own cryptocurrencies, interest in using them as a means of payment increases.</p>
</div>

<section class="abs partners" aria-label="Partners"></section>
<div class="abs partner" style="left:114px">CORALT</div>
<div class="abs partner" style="left:264px">BRENWICK</div>
<div class="abs partner" style="left:390px">ASHLEN</div>
<div class="abs partner" style="left:528px">KESTROW</div>
<div class="abs partner" style="left:669px">MIRELLA</div>
<div class="abs partner" style="left:810px">PAVO</div>
<div class="abs partner" style="left:947px">TESSURO</div>

<footer class="abs site-footer"></footer>
<div class="abs footer-head" style="left:132px">LINKS</div>
<div class="abs footer-link" style="left:132px;top:2594px">Home</div>
<div class="abs footer-link" style="left:132px;top:2622px">Services</div>
<div class="abs footer-link" style="left:132px;top:2650px">Portfolio</div>
<div class="abs footer-link" style="left:214px;top:2594px">About</div>
<div class="abs footer-link" style="left:214px;top:2622px">Partners</div>
<div class="abs footer-link" style="left:214px;top:2650px">Contact Us</div>
<div class="abs footer-head" style="left:359px">GET IN TOUCH</div>
<div class="abs footer-link" style="left:359px;top:2594px">Phone : 555 014 2290</div>
<div class="abs footer-link" style="left:359px;top:2622px">Email : info@vextor-mail.se</div>
<div class="abs footer-head" style="left:579px">CONTACT US</div>
<div class="abs field" style="left:581px;top:2598px;width:207px;height:32px">Name</div>
<div class="abs field" style="left:581px;top:2638px;width:207px;height:32px">Email</div>
<div class="abs field" style="left:796px;top:2598px;width:205px;height:72px">Mesage</div>
<div class="abs send-btn">SEND</div>
<div class="abs footer-rule"></div>
<div class="abs copyright">Copyright &copy; 2018 Vextor.&nbsp; All rights reserved.</div>
<div class="abs social-dot" style="left:975px" aria-label="Social link"></div>
<div class="abs social-dot" style="left:1011px" aria-label="Social link"></div>
<div class="abs social-dot" style="left:1052px" aria-label="Social link"></div>

</body>
</html>
```